Non fiction leadership Book Cover design needed for “Stay Bold: Build On Lasting Discipline”

I need a front cover design for a new book 6 X 9 traditional non-fiction book.

Title: "Stay BOLD - Build On Lasting Discipline"

The subtitle is not finalized- so use 2 lines of smaller dummy text

My brand guide is attached (please use the tan color sparingly)

I'd like to see BOLD look like it is in motion and "flying" across the page

Need CREATIVE designs and options

Do not want my picture on the front cover - I do want it on the back cover.

On the front cover I’d like to see creative use of font to create movement on “BOLD”

Target Market(s)

Business leaders

Industry/Entity Type

Aviation

Font styles to use
Other font styles liked:
• See style guide- can add additional font (modern script or san serif)

Colors
0054AA
0677BA
7BADD7
CADEEF
E8F1F8
EB3D1F
EC4F4E
F09395
F8D3D4
FCEDEE

Requirements
Must have
• Creative font use, using perspective to create movement/motion on BOLD
Should not have
• My picture on the front cover- my picture should be on the back cover

```html
<!DOCTYPE html>
<html lang="en">
<head>
<meta charset="utf-8">
<title>Stay Bold: Build On Lasting Discipline — Book Cover</title>
<link href="https://fonts.googleapis.com/css2?family=Montserrat:wght@400;500;600&family=Saira+Extra+Condensed:wght@700&display=swap" rel="stylesheet">
<style>
  :root {
    --backdrop: #060818;
    --paper: #faf2ec;
    --ink: #0b0d1a;
    --signal-red: #e3252c;
  }
  * { margin: 0; padding: 0; box-sizing: border-box; }
  html, body {
    width: 1200px;
    height: 1200px;
    overflow: hidden;
    background: var(--backdrop);
  }
  .stage {
    position: relative;
    width: 1200px;
    height: 1200px;
    background: var(--backdrop);
  }
  .book-cover {
    position: absolute;
    left: 230px;
    top: 44px;
    width: 741px;
    height: 1111px;
    background: var(--paper);
    overflow: hidden;
  }
  .title-lead {
    position: absolute;
    left: 78px;
    top: 96px;
    font-family: "Saira Extra Condensed", sans-serif;
    font-weight: 700;
    font-size: 124px;
    line-height: 1;
    letter-spacing: 16px;
    color: var(--ink);
  }
  .title-mark {
    position: absolute;
    left: 0;
    top: 0;
    width: 741px;
    height: 1111px;
  }
  .title-mark .glyph {
    fill: var(--signal-red);
    fill-rule: evenodd;
  }
  .title-mark .letters {
    filter: drop-shadow(0 14px 16px rgba(255, 255, 255, 0.95));
  }
  .subtitle {
    position: absolute;
    left: 0;
    width: 100%;
    top: 850px;
    text-align: center;
    font-family: "Montserrat", sans-serif;
    font-weight: 600;
    font-size: 43px;
    letter-spacing: -0.5px;
    color: var(--ink);
  }
  .teaser {
    position: absolute;
    left: 0;
    width: 100%;
    top: 924px;
    text-align: center;
    font-family: "Montserrat", sans-serif;
    font-weight: 400;
    font-size: 14.5px;
    line-height: 19px;
    color: var(--ink);
  }
  .author {
    position: absolute;
    left: 0;
    width: 100%;
    top: 1000px;
    text-align: center;
    font-family: "Montserrat", sans-serif;
    font-weight: 500;
    font-size: 44px;
    color: var(--signal-red);
  }
</style>
</head>
<body>
<main class="stage">
  <article class="book-cover">
    <div class="title-lead">STAY</div>

    <svg class="title-mark" viewBox="0 0 900 1350" role="img" aria-label="BOLD">
      <g class="letters">
        <!-- B -->
        <g transform="translate(51 250) skewY(14)">
          <path class="glyph" d="M0 0 H110 L160 50 V250 L135 275 L160 300 V550 L110 600 H0 Z
                                 M60 60 H95 L100 65 V240 H60 Z
                                 M60 310 H100 V535 L95 540 H60 Z"/>
        </g>
        <!-- O -->
        <g transform="translate(246 300) skewY(-20)">
          <path class="glyph" d="M40 0 H120 L160 40 V560 L120 600 H40 L0 560 V40 Z
                                 M60 60 H100 V540 H60 Z"/>
        </g>
        <!-- L -->
        <g transform="translate(451 230) skewY(16)">
          <path class="glyph" d="M0 0 H60 V540 H160 V600 H0 Z"/>
        </g>
        <!-- D -->
        <g transform="translate(656 230) skewY(-22)">
          <path class="glyph" d="M0 0 H100 L160 60 V540 L100 600 H0 Z
                                 M60 60 H90 L100 70 V530 L90 540 H60 Z"/>
        </g>
      </g>
    </svg>

    <h2 class="subtitle">Build On Lasting Discipline</h2>
    <p class="teaser">Lorem ipsum dolor sit amet, consectetuer adipiscing elit,<br>sed diam nonummy nibh euismod tincidunt</p>
    <p class="author">Margaret Ellison</p>
  </article>
</main>
</body>
</html>
```